Computer consultant business card

Bexil Software is a newly started computer consulting company. It's a small one-man company that provides mostly Vornix applications but also websites in collaboration with designers. I'm running this company on the side of full time university studies.

I want the final design to be clean and memorable. Be creative! :)

Some inspiration:
http://www.pixelmarta.com/design/48317
http://www.pixelmarta.com/design/2739164/business-card-design-by-frostlynk
http://www.pixelmarta.com/design/604281/business-card-design-by-koralind-vestrabanu

See attachment for my company logo.
Updates

I would like to thank everyone for submitting! I'll need a couple of days to review and ultimately select a design.

Target Market(s)

Non-technical entrepreneurs and small companies.

Industry/Entity Type

University

Requirements
Must have
• My company logo.
In any way, both colors from my logo.
First- and last name, e-mail and phone number.
Double-sided design.
Nice to have
• Something creative with the symbol in my logo

```html
<!DOCTYPE html>
<html lang="en">
<head>
<meta charset="utf-8">
<title>Bexil Software – Business Card</title>
<link rel="stylesheet" href="https://fonts.googleapis.com/css2?family=Open+Sans:wght@400;600;700&display=swap">
<style>
  :root {
    --brand-blue: #2179f5;
    --brand-dark: #34383c;
    --card-white: #ffffff;
    --divider: #c9ccd0;
    --backdrop: #e9e6e1;
  }
  * { margin: 0; padding: 0; box-sizing: border-box; }
  html, body { width: 1200px; height: 823px; overflow: hidden; }
  body {
    background: var(--backdrop);
    font-family: "Open Sans", Arial, sans-serif;
    position: relative;
  }
  .card {
    position: absolute;
    width: 540px;
    height: 310px;
    border-radius: 30px;
    overflow: hidden;
    box-shadow: 0 6px 18px rgba(0,0,0,0.18);
  }
  .card--front { left: 70px; top: 100px; background: var(--card-white); }
  .card--back { left: 600px; top: 420px; background: var(--brand-blue); }

  .card__wave { position: absolute; left: 0; top: 0; width: 540px; height: 310px; }

  .brand {
    position: absolute;
    left: 62px; top: 100px;
    display: flex; align-items: center; gap: 16px;
  }
  .brand__dot {
    width: 52px; height: 52px; border-radius: 50%;
    background: var(--brand-blue);
  }
  .brand__name {
    font-size: 64px; font-weight: 600; line-height: 1;
    color: var(--brand-dark); letter-spacing: 1px;
  }

  .contact {
    position: absolute;
    left: 296px; top: 58px;
    padding-left: 16px;
    border-left: 2px solid var(--divider);
    height: 120px;
  }
  .contact__first { font-size: 22px; font-weight: 700; color: var(--brand-blue); line-height: 1.1; }
  .contact__last { font-size: 17px; color: var(--brand-dark); line-height: 1.2; margin-bottom: 18px; }
  .contact__line {
    display: flex; align-items: center; gap: 8px;
    font-size: 15px; color: var(--brand-dark); line-height: 1.6;
  }
  .contact__icon { width: 12px; height: 12px; flex: none; }

  .address {
    position: absolute; left: 48px; bottom: 22px;
    color: var(--card-white); font-size: 14px; line-height: 1.35;
  }

  .back__brand {
    position: absolute; inset: 0;
    display: flex; align-items: center; justify-content: center;
    color: var(--card-white); font-size: 96px; font-weight: 600;
    letter-spacing: 2px;
  }
</style>
</head>
<body>

  <section class="card card--front" aria-label="Business card front">
    <svg class="card__wave" viewBox="0 0 540 310" aria-hidden="true">
      <path d="M0,236 C140,196 300,236 410,214 C470,202 510,186 540,176 L540,310 L0,310 Z" fill="var(--brand-dark)"/>
      <path d="M0,250 C140,206 300,244 410,220 C470,208 510,190 540,180 L540,310 L0,310 Z" fill="var(--card-white)"/>
      <path d="M0,256 C140,214 300,250 410,226 C470,214 510,194 540,184 L540,310 L0,310 Z" fill="var(--brand-blue)"/>
    </svg>

    <div class="brand">
      <span class="brand__dot"></span>
      <span class="brand__name">bexil</span>
    </div>

    <div class="contact">
      <p class="contact__first">First Name</p>
      <p class="contact__last">Last Name</p>
      <p class="contact__line">
        <svg class="contact__icon" viewBox="0 0 12 12" aria-hidden="true">
          <circle cx="6" cy="6" r="5.2" fill="none" stroke="var(--brand-blue)" stroke-width="1.4"/>
          <path d="M4,3.4 L5.2,3.4 L5.4,5 L4.7,5.5 C5.1,6.4 5.7,7 6.5,7.4 L7,6.7 L8.6,6.9 L8.6,8.1 C6,8.3 3.8,6.1 4,3.4 Z" fill="var(--brand-blue)"/>
        </svg>
        0123 456789
      </p>
      <p class="contact__line">
        <svg class="contact__icon" viewBox="0 0 12 12" aria-hidden="true">
          <rect x="1" y="2.5" width="10" height="7" rx="1.2" fill="var(--brand-blue)"/>
          <path d="M1.5,3.2 L6,6.6 L10.5,3.2" fill="none" stroke="var(--card-white)" stroke-width="1"/>
        </svg>
        info@bexil.com
      </p>
    </div>

    <p class="address">00, Complex name<br>City, State 0042</p>
  </section>

  <section class="card card--back" aria-label="Business card back">
    <span class="back__brand">bexil</span>
  </section>

</body>
</html>
```